Fahrzeugaufbereitung inkl. Hol- und Bringedienst
Zielgruppe
Für Privatkunden
Aufgabenstellung
Benötige einen Flyer, um Privatkunden unseren neuen Hol- und Bringedienst für Fahrzeugaufbereitung vorzustellen.
Text und Preise unter www.belvo-fahrdienst.de unter Fahrzeugaufbereitung.
Format Din Lang (105x210mm), zweiseitig

```html
<!DOCTYPE html>
<html lang="de">
<head>
<meta charset="utf-8">
<title>BELVO – Fahrzeugaufbereitung</title>
<link href="https://fonts.googleapis.com/css2?family=Roboto+Condensed:wght@400;700&family=Oswald:wght@600&display=swap" rel="stylesheet">
<style>
  :root {
    --bg: #e9e6e1;
    --blue: #2ea3dc;
    --blue-soft: #7cc6ea;
    --orange: #f07d1f;
    --ink: #1e1e1e;
    --grey: #e4e4e4;
    --white: #ffffff;
    --rule: #9a9a9a;
  }
  * { box-sizing: border-box; margin: 0; padding: 0; }
  html, body { width: 1200px; height: 1200px; overflow: hidden; }
  body {
    background: var(--bg);
    font-family: "Roboto Condensed", Arial, sans-serif;
    color: var(--ink);
    position: relative;
  }
  .flyer {
    position: absolute;
    left: 80px;
    width: 1040px;
    height: 520px;
    background: var(--white);
    box-shadow: 0 6px 18px rgba(0,0,0,.18);
    overflow: hidden;
  }
  .flyer--front { top: 60px; }
  .flyer--back { top: 620px; }

  .brand {
    position: absolute;
    display: flex;
    align-items: center;
    gap: 14px;
    color: var(--blue);
    font-weight: 700;
    font-size: 56px;
    line-height: 1;
  }
  .brand__dot { width: 18px; height: 18px; border-radius: 50%; background: var(--blue); }

  /* front */
  .front__head { position: absolute; inset: 0 0 330px 0; }
  .front__head .brand { left: 50px; top: 62px; }
  .front__divider { position: absolute; left: 320px; top: 30px; width: 2px; height: 130px; background: var(--rule); }
  .front__title { position: absolute; left: 360px; top: 52px; }
  .front__title h1 { font-size: 38px; font-weight: 700; line-height: 1.05; }
  .front__title p { font-size: 28px; margin-top: 6px; }
  .price { position: absolute; right: 60px; top: 34px; color: var(--orange); display: flex; align-items: flex-end; font-family: "Oswald", sans-serif; font-weight: 600; }
  .price__label { font-family: "Roboto Condensed", sans-serif; font-weight: 700; font-size: 26px; margin-right: 10px; margin-bottom: 22px; }
  .price__euro { font-size: 96px; line-height: 1; }
  .price__cent { font-size: 46px; line-height: 1; align-self: flex-start; margin-top: 6px; }

  .front__steps { position: absolute; left: 0; right: 0; bottom: 0; height: 330px; background: var(--blue); color: var(--white); }
  .front__steps h2 { position: absolute; left: 50px; top: 28px; font-size: 34px; font-weight: 700; }
  .steps { position: absolute; left: 50px; right: 50px; top: 90px; display: flex; align-items: center; justify-content: space-between; }
  .step {
    width: 190px; height: 190px;
    border: 2px solid var(--white);
    border-radius: 50%;
    background: radial-gradient(circle, var(--blue-soft) 0%, var(--blue) 75%);
  }
  .step-arrow { width: 34px; height: 34px; }

  /* back */
  .back__head { position: absolute; inset: 0 0 290px 0; }
  .back__head .brand { left: 50px; top: 66px; }
  .contact { position: absolute; left: 500px; top: 28px; font-size: 21px; line-height: 1.45; }
  .contact h3 { color: var(--orange); font-size: 30px; font-weight: 700; margin-bottom: 6px; }
  .contact__cols { display: flex; gap: 60px; }
  .back__body { position: absolute; left: 0; right: 0; bottom: 0; height: 290px; background: var(--grey); display: flex; padding: 30px 50px 0; gap: 70px; }
  .back__body h3 { color: var(--blue); font-size: 30px; font-weight: 400; margin-bottom: 10px; }
  .service { width: 440px; font-size: 20px; line-height: 1.4; }
  .service .note { font-size: 14px; margin-top: 8px; }
  .offer ul { list-style: none; font-size: 20px; line-height: 1.45; }
  .offer li::before { content: "• "; }
</style>
</head>
<body>

<section class="flyer flyer--front">
  <header class="front__head">
    <div class="brand"><span class="brand__dot"></span><span>BELVO</span></div>
    <span class="front__divider"></span>
    <div class="front__title">
      <h1>Fahrzeugaufbereitung</h1>
      <p>inkl. Hol- und Bringedienst</p>
    </div>
    <div class="price">
      <span class="price__label">nur €</span>
      <span class="price__euro">59,</span>
      <span class="price__cent">90*</span>
    </div>
  </header>

  <div class="front__steps">
    <h2>Und so funktioniert's:</h2>
    <div class="steps">
      <div class="step" role="img" aria-label="Piktogramm: Anruf per Mobiltelefon"></div>
      <svg class="step-arrow" viewBox="0 0 34 34" aria-hidden="true"><path d="M4 11h14V3l14 14-14 14v-8H4z" fill="#fff"/></svg>
      <div class="step" role="img" aria-label="Piktogramm: Abholung des Fahrzeugs am Wunschort"></div>
      <svg class="step-arrow" viewBox="0 0 34 34" aria-hidden="true"><path d="M4 11h14V3l14 14-14 14v-8H4z" fill="#fff"/></svg>
      <div class="step" role="img" aria-label="Piktogramm: Aufbereitung und Kontrolle des Fahrzeugs"></div>
      <svg class="step-arrow" viewBox="0 0 34 34" aria-hidden="true"><path d="M4 11h14V3l14 14-14 14v-8H4z" fill="#fff"/></svg>
      <div class="step" role="img" aria-label="Piktogramm: Rückgabe des sauberen Fahrzeugs"></div>
    </div>
  </div>
</section>

<section class="flyer flyer--back">
  <header class="back__head">
    <div class="brand"><span class="brand__dot"></span><span>BELVO</span></div>
    <div class="contact">
      <h3>Kontakt</h3>
      <div class="contact__cols">
        <p>B.E.L.V.O GmbH<br>Lindenhofstr. 27<br>10969 Berlin</p>
        <p>Tel. 030 41 72 55 3 -0<br>Mail info@belvo-fahrdienst.de<br>Web www.belvo-fahrdienst.de</p>
      </div>
    </div>
  </header>
  <div class="back__body">
    <div class="service">
      <h3>Unser Service für Sie</h3>
      <p>Wir bieten Ihnen eine klassische <strong>Fahrzeugaufbereitung inkl. Hol- und Bringedienst</strong> für nur <strong>€ 59,90*</strong> an. Sparen Sie Ihre wertvolle Zeit und lassen Sie Ihr Fahrzeug von uns an Ihrem Wunschort abholen und innerhalb der nächsten <strong>90 Minuten</strong> aufbereiten.</p>
      <p class="note">*Preis inkl. MwSt. und freibleibend.</p>
    </div>
    <div class="offer">
      <h3>Unser Leistungsangebot enthält</h3>
      <ul>
        <li>Hol- und Bringeservice</li>
        <li>Aussenwäsche inkl. Felgenreinigung</li>
        <li>Innenreinigung inkl. Cockpit und Saugen</li>
        <li>Fensterreinigung innen &amp; aussen</li>
        <li>Öl-, Wasser- und Wischwasserkontrolle</li>
        <li>Reifendruck und Profilkontrolle</li>
      </ul>
    </div>
  </div>
</section>

</body>
</html>
```